Marwick Law Letterhead

We need a new letterhead design for a Law Firm. The address for the law firm is 1475 Calloway Street, Suite 210, Houston, Texas 77041. Phone Number: 832-361-9027; Fax Number: 832-614-7359. The logo is uploaded to the project.

```html
<!DOCTYPE html>
<html lang="en">
<head>
<meta charset="utf-8">
<title>Marwick Law Letterhead</title>
<link href="https://fonts.googleapis.com/css2?family=Montserrat:wght@400;500;600&display=swap" rel="stylesheet">
<style>
  :root {
    --bg: #ececec;
    --paper: #ffffff;
    --navy: #1b2d5e;
    --red: #c4162a;
    --red-dark: #6e0a16;
    --ink: #2a2a2a;
    --muted: #444;
  }
  * { box-sizing: border-box; margin: 0; padding: 0; }
  html, body {
    width: 1200px; height: 960px; overflow: hidden;
    background: var(--bg);
    font-family: "Montserrat", Arial, sans-serif;
  }
  .letterhead {
    position: absolute; left: 282px; top: 30px;
    width: 636px; height: 900px;
    background: var(--paper);
    box-shadow: 0 2px 10px rgba(0,0,0,.12);
    overflow: hidden;
  }
  .brand {
    position: absolute; left: 48px; top: 62px;
    display: flex; align-items: center; gap: 10px;
  }
  .brand-dot { width: 18px; height: 18px; border-radius: 50%; background: var(--navy); }
  .brand-name { font-size: 26px; font-weight: 600; color: var(--navy); letter-spacing: .5px; }
  .contact {
    position: absolute; left: 420px; top: 48px;
    padding-left: 16px; border-left: 1.5px solid var(--red);
    font-size: 11px; line-height: 1.45; color: var(--ink);
  }
  .contact-line { display: flex; align-items: center; gap: 6px; }
  .contact-line svg { width: 11px; height: 11px; flex: none; }
  .contact address { font-style: normal; margin-bottom: 4px; }
  .recipient {
    position: absolute; left: 50px; top: 200px;
    font-size: 12px; line-height: 1.45; color: var(--ink);
  }
  .recipient span { display: block; }
  .recipient .indent-1 { padding-left: 12px; }
  .recipient .indent-2 { padding-left: 24px; }
  .recipient .indent-3 { padding-left: 36px; }
  .body-copy {
    position: absolute; left: 50px; top: 290px; width: 530px;
    font-size: 11px; line-height: 1.5; color: var(--muted);
  }
  .body-copy p { margin-bottom: 16px; }
  .sign-off {
    position: absolute; left: 50px; top: 735px;
    font-size: 14px; color: var(--ink);
  }
  .signature {
    display: block; margin-top: 8px; margin-left: 10px;
    width: 100px; height: 30px; border-radius: 4px;
    background: linear-gradient(90deg, #d9d9d9, #f2f2f2);
  }
  .swoosh { position: absolute; inset: 0; width: 636px; height: 900px; }
</style>
</head>
<body>
  <main class="letterhead">
    <svg class="swoosh" viewBox="0 0 636 900" aria-hidden="true">
      <defs>
        <linearGradient id="redBand" x1="1" y1="0" x2="0.4" y2="1">
          <stop offset="0" stop-color="var(--red)"/>
          <stop offset="1" stop-color="var(--red-dark)"/>
        </linearGradient>
      </defs>
      <path d="M636 700 Q560 850 250 900 L636 900 Z" fill="url(#redBand)"/>
      <path d="M0 900 Q490 860 622 672 L636 672 L636 690 Q500 875 30 900 Z" fill="var(--navy)"/>
    </svg>

    <div class="brand">
      <span class="brand-dot"></span>
      <span class="brand-name">Marwick Law</span>
    </div>

    <div class="contact">
      <address>1475 Calloway Street,<br>Suite 210, Houston,<br>Texas 77041</address>
      <div class="contact-line">
        <svg viewBox="0 0 12 12"><circle cx="6" cy="6" r="6" fill="var(--red)"/><path d="M4 3.2 L5 3 L5.6 4.6 L5 5.1 Q5.6 6.5 6.9 7 L7.4 6.4 L9 7 L8.8 8 Q6.9 8.6 5.1 6.9 Q3.4 5.1 4 3.2Z" fill="#fff"/></svg>
        <span>832-361-9027</span>
      </div>
      <div class="contact-line">
        <svg viewBox="0 0 12 12"><circle cx="6" cy="6" r="6" fill="var(--red)"/><rect x="3.3" y="5" width="5.4" height="3" fill="#fff"/><rect x="4.2" y="3.2" width="3.6" height="1.5" fill="#fff"/></svg>
        <span>832-614-7359</span>
      </div>
    </div>

    <div class="recipient">
      <span>Mr/s</span>
      <span class="indent-1">First Name and Last Name</span>
      <span class="indent-2">Company Name</span>
      <span class="indent-3">Address</span>
    </div>

    <section class="body-copy">
      <p>Lorem ipsum dolor sit amet,consectetur adipiscing sed do eiusmod tempor incididunt laboreet dolore magna aliqua.Ut enim ad minim,veniam, quis nostrud exercitation ullamco laboris nisi ut aliquip exea commodo consequat.Lorem ipsum dolor sit amet,consectetur adipiscing sed do eiusmod tempor incididunt.labore et dolore magna aliqua. Ut enim</p>
      <p>Lorem ipsum dolor sit amet, consectetur adipiscing sed do eiusmod tempor incididunt labore et dolore magna aliqua. Ut enim ad minim veniam, quis nostrud exercitation ullamco laboris nisi ut aliquip exea commodo consequat.Duis aute irure dolor in reprehenderit in voluptate velit esse cillum irure dolor in reprehenderit in voluptate velit esse irure</p>
      <p>Lorem ipsum dolor sit amet, consectetur adipiscing sed do eiusmod tempor incididunt labore et dolore magna aliqua. consequat. Duis aute irure dolor in.reprehenderit in voluptate velit esse cillum dolore eu fugiat nulla pariatur. Excepteur sint occaecat cupidatat non proident, sunt in culpa qui officia deserunt mollit,</p>
      <p>Lorem ipsum dolor sit amet, consectetur adipiscing sed do eiusmod tempor incididunt labore et dolore magna aliqua. Ut enim Lorem ipsum dolor sit amet, consectetur adipiscing sed do eiusmod tempor incididunt labore et dolore magna aliqua. Ut enim Lorem ipsum aliqua.ipsum</p>
      <p>Lorem ipsum dolor sit amet, consectetur adipiscing sed do eiusmod tempor incididunt labore et dolore magna aliqua. Ut enim ad minim veniam, quis nostrud exercitation ullamco laboris nisi ut aliquip exea commodo consequat.Duis aute irure dolor in reprehenderit in voluptate velit esse cillum irure dolor in reprehenderit in voluptate velit esse irure</p>
    </section>

    <div class="sign-off">
      Regards
      <span class="signature" role="img" aria-label="Handwritten signature"></span>
    </div>
  </main>
</body>
</html>
```